Community coffee table book/quiz book

I need a couple of things for my book:
- Book cover (Title: "1000 spørsmål om Kvernhaugen")
- "Cover pages" for each chapter of the book (15-16 chapters)
- "Watermark" or background design for all the pages of the book.
- A cover image for the book's Kretsbok page.
- Design of a paper "belt"

The book:
The book will consist of about 200+ pages with ten questions on one page and ten answers on the next.

The name of the book is "1000 spørsmål om Kvernhaugen" which means 1000 questions about Fyllingsdalen (Fyllingsdalen is a suburb of the city Bergen in Norway). Author is Helge Myrvold.
The questions in the book are grouped in chapters like:
History
Facts
Schools
Businesses
People/profiles
Sport
Culture
Buildings/Landmarks/Sculptures
The different areas of the suburb
The city
Language/expressions
Nature
The names of the chapters are not set, so it would be good to have the option to change the title of the pages without having to contact the designer (maybe by adding the text on top of the cover page?). I therefore suggest that these images are without text.
The book size is 18X18 cm.

The chapter cover pages:
The book will basically consist of text. Ten questions on one page, and ten questions on the next. Visually it will be quite "boring" to look at. I would therefore like to have a chapter cover page for each chapter, preferable in colour.

Water mark:
To avoid having a book full of white pages with limited amount of text I thought of having some kind of design on each page. I do not know how this should be done, but maybe it is possible to create some kind of background image or watermark image with similar design as the book cover and the chapter covers?

The Kretsbok cover image:
This should be the same as, or similar to, the book cover.
I believe the optimal size is 828px x 315px?

Paper "belt":
The book is to be sold for charity. The receiver of the money is the local sports club. I would like to have the book "wrapped in a 5-6 cm wide paper belt with the logo of the sports club (please see logo and colours here: http://www.ilbrattlia.no). I do not think that the book cover itself should have the sports club's color (purple), but maybe the paper band could? (Again: YOU are the designer)

Photos:
I reckon you would like some photos for both the book cover and the chapter covers. I will of course do the best I can to provide these photos when I have selected a designer. I the meantime

Target Market(s)

Target market is middle clas men and women 35+ from the geographical area Fyllingsdalen.

Industry/Entity Type

Community

Font styles to use
Serif
Sans Serif

Requirements
Must have
• The book will be sold by children on doors. The buyers will probably take a look briefly through the book and then decide if they are going to buy.
• It is important that they like the question types, categories and some of the actual questions they read. But it is also important that they like the look of the book. Therefore the book cover and the chapter cover pages must be appealing enough for the buyers to want this book on theor coffee table.
Nice to have
• I have uploaded a short video clip to Vidtrekk (https://www.vidtrekk.example/watch?v=qx7Ta2Lm9pz). This a promo clip from Pimlo Kanalen. I felt inspired when I saw it and thought that backgrounds like the ones used in the promo could also be used as backgrounds for each chapter's cover pages. Maybe different colour for each chapter? Screenshots from the clip is uploaded below.
• Then again: Maybe I am an idiot? YOU are the designer :-)
Should not have
• There has been some rivalry between two sportsclubs in the region after the clubs was merged a couple of years ago. I therefore believe we should therefore try avoid both the old clubs' colours (blue&yellow and green) and the new club's colour (purple).

```html
<!DOCTYPE html>
<html lang="en">
<head>
<meta charset="utf-8">
<title>Chapter Cover Pages</title>
<link href="https://fonts.googleapis.com/css2?family=Josefin+Sans:wght@400&family=PT+Sans+Narrow&display=swap" rel="stylesheet">
<style>
  :root {
    --canvas: #ffffff;
    --page: #f2f2f2;
    --skyline: #e6e6e6;
    --accent: #ffc805;
    --ink: #000000;
    --dot: #ffffff;
  }
  html, body {
    margin: 0;
    padding: 0;
    overflow: hidden;
  }
  .canvas {
    position: relative;
    width: 1200px;
    height: 1000px;
    background: var(--canvas);
    overflow: hidden;
  }
  .chapter-cover {
    position: absolute;
    top: 213px;
    width: 492px;
    height: 492px;
    background: var(--page);
    overflow: hidden;
  }
  .chapter-cover--history { left: 86px; }
  .chapter-cover--culture { left: 649px; }
  .chapter-cover__art {
    position: absolute;
    inset: 0;
    width: 492px;
    height: 492px;
  }
  .chapter-cover__skyline { fill: var(--skyline); }
  .chapter-cover__wave { fill: var(--accent); }
  .chapter-cover__title {
    position: absolute;
    left: 0;
    right: 0;
    top: 213px;
    display: flex;
    justify-content: center;
    align-items: center;
    gap: 14px;
    font-family: "Josefin Sans", sans-serif;
    font-weight: 400;
    font-size: 42px;
    line-height: 1;
    letter-spacing: 0.28em;
    color: var(--accent);
  }
  .chapter-cover__title-text {
    position: relative;
    margin-right: -0.28em;
    padding-top: 6px;
  }
  .chapter-cover__title-text::after {
    content: "";
    position: absolute;
    left: 2px;
    right: 0.28em;
    bottom: -16px;
    border-bottom: 3px dotted var(--accent);
  }
  .chapter-cover__dot {
    width: 11px;
    height: 11px;
    border-radius: 50%;
    background: var(--dot);
  }
  .caption {
    position: absolute;
    left: 0;
    right: 0;
    top: 736px;
    margin: 0;
    text-align: center;
    font-family: "PT Sans Narrow", sans-serif;
    font-weight: 400;
    font-size: 78px;
    line-height: 1;
    color: var(--ink);
  }
</style>
</head>
<body>
  <main class="canvas">
    <section class="chapter-cover chapter-cover--history">
      <svg class="chapter-cover__art" viewBox="0 0 492 492" aria-hidden="false">
        <rect class="chapter-cover__skyline" x="0" y="318" width="492" height="174" role="img" aria-label="City skyline silhouette"/>
        <path class="chapter-cover__wave" d="M0,0 H492 V38 C330,12 80,0 0,61 Z"/>
        <path class="chapter-cover__wave" d="M0,452 C20,425 45,411 66,412 C82,413 94,419 104,427 C200,470 360,480 492,452 V492 H0 Z"/>
      </svg>
      <h2 class="chapter-cover__title">
        <span class="chapter-cover__dot"></span>
        <span class="chapter-cover__title-text">HISTORY</span>
        <span class="chapter-cover__dot"></span>
      </h2>
    </section>

    <section class="chapter-cover chapter-cover--culture">
      <svg class="chapter-cover__art" viewBox="0 0 492 492" aria-hidden="false">
        <rect class="chapter-cover__skyline" x="0" y="318" width="492" height="174" role="img" aria-label="City skyline silhouette"/>
        <path class="chapter-cover__wave" d="M0,0 H492 V38 C330,12 80,0 0,61 Z"/>
        <path class="chapter-cover__wave" d="M0,452 C20,425 45,411 66,412 C82,413 94,419 104,427 C200,470 360,480 492,452 V492 H0 Z"/>
      </svg>
      <h2 class="chapter-cover__title">
        <span class="chapter-cover__dot"></span>
        <span class="chapter-cover__title-text">CULTURE</span>
        <span class="chapter-cover__dot"></span>
      </h2>
    </section>

    <p class="caption">COVER PAGES</p>
  </main>
</body>
</html>
```